Custom Manufacturing Company square space website design

I own a custom manufacturing company that uses precision cutting technology to manufacture project components over a couple industries. We have an industrial CNC router and state of the art edge bander and cut a lot of cabinetry components for cabinet shops, builders, closet companies, ect. We offer design and assembly for any cabinetry or can build cabinets to spec. We also cut components for other industries out of wood, plastics, acryclics, ect. We offer design engineering services, product development protype services. we have a 3D printer farm. We want our communicate trust, dependability, and the value we place on client relationships.

We essentially want a credibility website. Landing page and drops downs for services we offer, capabilites, about us, contact

```html
<!DOCTYPE html>
<html lang="en">
<head>
<meta charset="utf-8">
<title>Northline Fabrication — Custom Part Development</title>
<link href="https://fonts.googleapis.com/css2?family=Oswald:wght@400;500;600&family=Nunito:wght@400;600;700&family=Michroma&display=swap" rel="stylesheet">
<style>
:root{
  --ink:#111111;
  --text:#2b2b2b;
  --muted:#8a8a8a;
  --line:#9a9a9a;
  --paper:#ffffff;
  --mist:#f5f5f5;
  --night:#1b1b1b;
  --steel-dark:#3d5575;
  --steel-light:#aab8c8;
}
*{box-sizing:border-box;margin:0;padding:0}
html,body{width:1200px;height:4448px;overflow:hidden}
body{position:relative;background:var(--paper);font-family:'Nunito',sans-serif;color:var(--text)}
.band{position:absolute;left:0;width:1200px}
h2.section-title{position:absolute;left:0;width:1200px;text-align:center;font-family:'Oswald',sans-serif;font-weight:500;font-size:31px;color:var(--ink)}
.btn-outline{position:absolute;border:1.5px solid var(--ink);background:var(--paper);font-family:'Oswald',sans-serif;font-weight:500;font-size:14px;color:var(--ink);display:flex;align-items:center;justify-content:center;white-space:nowrap}
.btn-solid{position:absolute;background:var(--ink);color:#fff;display:flex;align-items:center;justify-content:center;font-size:13px;white-space:nowrap}
.photo{position:absolute}

/* header */
.site-header{top:0;height:85px;background:var(--paper)}
.brand{position:absolute;left:163px;top:24px;display:flex;align-items:center;gap:9px}
.brand-mark{width:26px;height:26px;border:2px solid var(--ink)}
.brand-name{font-family:'Nunito',sans-serif;font-weight:700;font-size:13px;letter-spacing:1.5px;color:var(--ink);line-height:1.15}
.nav{position:absolute;left:410px;top:34px;display:flex;gap:26px;font-family:'Michroma',sans-serif;font-size:8.5px;letter-spacing:.6px;color:var(--ink);white-space:nowrap}
.nav-cta{left:882px;top:20px;width:156px;height:40px;font-family:'Michroma',sans-serif;font-size:8.5px;letter-spacing:.8px;font-weight:400}

/* hero */
.hero{top:85px;height:525px;background:linear-gradient(110deg,var(--steel-dark) 0%,#5f7897 45%,var(--steel-light) 75%,#d9a25a 88%,#6d7f95 100%)}
.hero h1{position:absolute;left:160px;top:160px;font-family:'Oswald',sans-serif;font-weight:500;font-size:35px;line-height:44px;color:#fff}
.hero p{position:absolute;left:160px;top:258px;font-size:27px;color:#fff}
.hero .btn-solid{left:161px;top:315px;width:149px;height:40px}

/* cards */
.service-card{position:absolute;top:763px;width:263px}
.service-card .photo{left:0;top:0;width:263px;height:160px}
.service-card .badge{position:absolute;left:114px;top:132px;width:36px;height:32px;background:#fff;clip-path:polygon(0 0,100% 0,50% 100%)}
.service-card p{position:absolute;top:180px;left:20px;width:223px;text-align:center;font-family:'Oswald',sans-serif;font-size:12.5px;line-height:22px;color:var(--ink)}

/* about */
.about{top:1092px;height:563px;background:var(--mist)}
.about h2{position:absolute;left:163px;top:98px;font-family:'Oswald',sans-serif;font-weight:500;font-size:31px;color:var(--ink)}
.about p{position:absolute;left:163px;top:164px;width:425px;font-size:12.5px;line-height:28.4px}
.about .btn-solid{left:161px;top:418px;width:135px;height:42px;font-family:'Oswald',sans-serif;font-size:14px}
.about .photo{left:670px;top:97px;width:330px;height:371px;background:linear-gradient(160deg,#c9cdd3 0%,#7b8390 40%,#2c3446 75%,#4c3a64 100%)}

/* stats */
.stat{position:absolute;top:1745px;width:220px}
.stat svg{display:block}
.stat .num{margin-top:10px;font-family:'Oswald',sans-serif;font-weight:600;font-size:36px;line-height:40px;color:var(--ink)}
.stat .label{margin-top:4px;font-size:14px;color:var(--text)}

/* process */
.process{top:1955px;height:545px;background:var(--mist)}
.step{position:absolute;top:2118px;width:158px;height:158px;border-radius:50%;background:#fff;border:1px solid #d6d6d6;display:flex;align-items:center;justify-content:center}
.step-label{position:absolute;top:2295px;width:200px;text-align:center;font-family:'Oswald',sans-serif;font-weight:500;font-size:15px;line-height:19px;color:var(--ink)}
.chev{position:absolute;top:2186px}

/* projects */
.project{position:absolute;top:2663px;width:263px}
.project .photo{left:0;top:0;width:263px;height:205px}
.project p{position:absolute;top:222px;left:3px;width:215px;font-family:'Oswald',sans-serif;font-size:12.5px;line-height:22px;color:var(--ink)}
.project svg{position:absolute;left:237px;top:233px}
.slider-arrow{position:absolute;width:38px;height:38px;display:flex;align-items:center;justify-content:center;background:var(--ink)}

/* capabilities */
.capabilities{top:3082px;height:480px;background:var(--mist)}
.cap{position:absolute;top:3218px;width:183px;height:187px;background:#fff;display:flex;flex-direction:column;align-items:center}
.cap svg{margin-top:46px}
.cap span{margin-top:20px;font-family:'Oswald',sans-serif;font-weight:500;font-size:15px;color:var(--ink)}
.cap.faded{opacity:.45;background:#fafafa}

/* contact */
.field{position:absolute;width:292px;border-bottom:1.3px solid var(--line);height:32px;font-size:11px;color:var(--muted)}
.field.filled{color:var(--ink)}

/* footer */
.footer{top:4112px;height:336px;background:var(--night);color:#fff}
.footer h4{position:absolute;font-family:'Oswald',sans-serif;font-weight:500;font-size:15px}
.quick-links{position:absolute;left:163px;top:116px;list-style:none;font-size:12px;line-height:27px}
.foot-brand{position:absolute;left:430px;top:85px;display:flex;align-items:center;gap:14px}
.foot-brand .brand-mark{width:44px;height:44px;border-color:#fff}
.foot-brand span{font-family:'Nunito',sans-serif;font-weight:700;font-size:21px;letter-spacing:3px;line-height:1.2}
.contact-row{position:absolute;left:818px;display:flex;gap:12px;font-size:13px;line-height:18px}
.divider{position:absolute;left:163px;top:273px;width:875px;height:1px;background:#444}
.copyright{position:absolute;left:163px;top:297px;font-size:12px}
.social{position:absolute;top:295px;width:22px;height:22px;border:1px solid #777}
</style>
</head>
<body>

<header class="band site-header">
  <div class="brand"><div class="brand-mark"></div><div class="brand-name">NORTHLINE<br>FABRICATION</div></div>
  <nav class="nav"><span>OUR SERVICES ⌄</span><span>CAPABILITES</span><span>ABOUT US</span><span>CONTACT US</span></nav>
  <div class="btn-outline nav-cta">REQUEST QUOTE</div>
</header>

<section class="band hero" role="img" aria-label="Laser cutting head throwing sparks over a perforated metal sheet">
  <h1>Custom Part Development<br>And Manufacturing</h1>
  <p>Let’s Bring Your Ideas To Life</p>
  <div class="btn-solid">Request Quote</div>
</section>

<h2 class="section-title" style="top:690px">What We Do</h2>
<div class="service-card" style="left:161px">
  <div class="photo" role="img" aria-label="Cabinet design drawing on a computer monitor" style="background:linear-gradient(135deg,#e6e6e4,#9a9c9f 60%,#6e6a62)"></div>
  <div class="badge"></div>
  <p>We Offer Design And Assembly For Any Cabinetry Or Can Build Cabinets To Specifications.</p>
</div>
<div class="service-card" style="left:468px">
  <div class="photo" role="img" aria-label="CNC cutter working on a sheet with sparks" style="background:linear-gradient(160deg,#2a2a22,#5b5a38 55%,#8e8a52)"></div>
  <div class="badge"></div>
  <p>We Also Cut Components For Other Industries Out Of Wood, Plastics, Acrylics, Etc.</p>
</div>
<div class="service-card" style="left:776px">
  <div class="photo" role="img" aria-label="Engineer reviewing a prototype part" style="background:linear-gradient(140deg,#1f3a78,#3c5fa0 50%,#c5cede)"></div>
  <div class="badge"></div>
  <p>We Offer Design Engineering Services, Product Development Protype Services.</p>
</div>

<section class="band about">
  <h2>About Us</h2>
  <p>Lorem ipsum dolor sit amet, consectetur adipiscing elit. Etiam suscipit lorem eget ligula tincidunt pharetra. Sed aliquam lacus et dolor tempus mollis. Etiam luctus, metus eget lobortis porttitor, arcu orci bibendum dolor, ut accumsan lacus nibh et nisi. Curabitur et pharetra orci. Sed vulputate erat risus. Sed lobortis nunc eleifend ornare ultrices. Mauris eget justo nisi. Nulla ultrices commodo orci ac vulputate. Nunc at leo quis elit tincidunt placerat. Nunc lacinia rutrum varius.</p>
  <div class="btn-solid">Read More</div>
  <div class="photo" role="img" aria-label="Operator at a CNC machine control panel"></div>
</section>

<div class="stat" style="left:163px">
  <svg width="50" height="42" viewBox="0 0 50 42" fill="none" stroke="#111" stroke-width="2"><rect x="2" y="10" width="46" height="30" rx="2"/><path d="M17 10V4h16v6M2 22h46M22 19h6v6h-6z"/></svg>
  <div class="num">20+</div><div class="label">Years of Experience</div>
</div>
<div class="stat" style="left:396px">
  <svg width="50" height="42" viewBox="0 0 50 42" fill="none" stroke="#111" stroke-width="2"><path d="M8 40V2M8 4h30v20H8M14 4v20M20 4v20M26 4v20M32 4v20M3 40h12"/></svg>
  <div class="num">100%</div><div class="label">Made in America</div>
</div>
<div class="stat" style="left:630px">
  <svg width="50" height="42" viewBox="0 0 50 42" fill="none" stroke="#111" stroke-width="2"><circle cx="21" cy="21" r="19"/><path d="M8 10c6 2 8 8 4 12s2 10 6 14M26 3c-2 6 4 8 8 8s4 8 0 12-2 10-4 14"/></svg>
  <div class="num">Global</div><div class="label">Servicimg &nbsp;the Globe</div>
</div>
<div class="stat" style="left:864px">
  <svg width="50" height="42" viewBox="0 0 50 42" fill="none" stroke="#111" stroke-width="2"><circle cx="19" cy="15" r="12"/><path d="M12 25l-3 15 10-5 10 5-3-15"/></svg>
  <div style="margin-top:10px;width:72px;height:30px;border:2px solid #111"></div>
  <div class="label">Industry Standatrds Met</div>
</div>

<section class="band process"></section>
<h2 class="section-title" style="top:1992px">Our Process</h2>
<div class="step" style="left:162px"><svg width="70" height="70" viewBox="0 0 70 70" fill="none" stroke="#111" stroke-width="2.2"><circle cx="35" cy="38" r="26"/><path d="M18 30c0-12 34-12 34 0M14 32h42M24 44c3 8 19 8 22 0M31 14v10M39 14v10"/></svg></div>
<div class="step" style="left:401px"><svg width="70" height="70" viewBox="0 0 70 70" fill="none" stroke="#111" stroke-width="2.2"><path d="M35 8l28 14-28 14L7 22zM7 34l28 14 28-14M7 46l28 14 28-14"/></svg></div>
<div class="step" style="left:640px"><svg width="70" height="70" viewBox="0 0 70 70" fill="none" stroke="#111" stroke-width="2.2"><path d="M12 8h46v8H12zM30 16h10v10H30zM35 26v8M8 58h54M16 52h38v6H16zM30 44l5-8 5 8"/></svg></div>
<div class="step" style="left:880px"><svg width="76" height="60" viewBox="0 0 76 60" fill="none" stroke="#111" stroke-width="2.2"><path d="M20 12h32v32H20zM52 22h12l8 10v12H52"/><circle cx="30" cy="46" r="5"/><circle cx="62" cy="46" r="5"/><path d="M4 22h12M8 30h10M2 38h14"/></svg></div>
<svg class="chev" style="left:339px" width="42" height="22" viewBox="0 0 42 22" fill="none" stroke-width="3"><path d="M2 3l8 8-8 8" stroke="#333"/><path d="M14 3l8 8-8 8" stroke="#777"/><path d="M26 3l8 8-8 8" stroke="#bbb"/></svg>
<svg class="chev" style="left:578px" width="42" height="22" viewBox="0 0 42 22" fill="none" stroke-width="3"><path d="M2 3l8 8-8 8" stroke="#333"/><path d="M14 3l8 8-8 8" stroke="#777"/><path d="M26 3l8 8-8 8" stroke="#bbb"/></svg>
<svg class="chev" style="left:817px" width="42" height="22" viewBox="0 0 42 22" fill="none" stroke-width="3"><path d="M2 3l8 8-8 8" stroke="#333"/><path d="M14 3l8 8-8 8" stroke="#777"/><path d="M26 3l8 8-8 8" stroke="#bbb"/></svg>
<div class="step-label" style="left:141px">Application<br>Engineering</div>
<div class="step-label" style="left:380px">Material<br>Selection</div>
<div class="step-label" style="left:619px">Part Fabrication</div>
<div class="step-label" style="left:859px">Delivery</div>
<div class="btn-outline" style="left:532px;top:2372px;width:135px;height:39px">Get Started</div>

<h2 class="section-title" style="top:2538px">Recent Projects</h2>
<div class="slider-arrow" style="left:100px;top:2747px"><svg width="16" height="12" viewBox="0 0 16 12" fill="none" stroke="#fff" stroke-width="1.6"><path d="M15 6H1M6 1L1 6l5 5"/></svg></div>
<div class="slider-arrow" style="left:1061px;top:2747px"><svg width="16" height="12" viewBox="0 0 16 12" fill="none" stroke="#fff" stroke-width="1.6"><path d="M1 6h14M10 1l5 5-5 5"/></svg></div>
<div class="project" style="left:161px">
  <div class="photo" role="img" aria-label="Worker grinding metal with sparks" style="background:linear-gradient(135deg,#2b2420,#6a4a35 50%,#b98a5c)"></div>
  <p>Lorem Ipsum Dolor Sit Consectetur Adipiscing Elit. Etiam Suscipit Lorem.</p>
  <svg width="18" height="12" viewBox="0 0 18 12" fill="none" stroke="#111" stroke-width="1.6"><path d="M1 6h16M12 1l5 5-5 5"/></svg>
</div>
<div class="project" style="left:468px">
  <div class="photo" role="img" aria-label="CNC router cutting a panel while an operator holds a tablet" style="background:linear-gradient(150deg,#9c8e80,#6e6a66 50%,#c0b6aa)"></div>
  <p>Lorem Ipsum Dolor Sit Consectetur Adipiscing Elit. Etiam Suscipit Lorem.</p>
  <svg width="18" height="12" viewBox="0 0 18 12" fill="none" stroke="#111" stroke-width="1.6"><path d="M1 6h16M12 1l5 5-5 5"/></svg>
</div>
<div class="project" style="left:776px">
  <div class="photo" role="img" aria-label="Welder working in a fabrication shop" style="background:linear-gradient(140deg,#3b3a2e,#5a4a3c 50%,#b4643a)"></div>
  <p>Lorem Ipsum Dolor Sit Consectetur Adipiscing Elit. Etiam Suscipit Lorem.</p>
  <svg width="18" height="12" viewBox="0 0 18 12" fill="none" stroke="#111" stroke-width="1.6"><path d="M1 6h16M12 1l5 5-5 5"/></svg>
</div>
<div class="btn-outline" style="left:537px;top:2955px;width:126px;height:39px">View All</div>

<section class="band capabilities"></section>
<h2 class="section-title" style="top:3110px">Our Capabilites</h2>
<div class="cap faded" style="left:0"><svg width="48" height="60" viewBox="0 0 48 60" fill="none" stroke="#111" stroke-width="2"><path d="M6 4h36v8H6zM18 12h12v10H18zM24 22v34M20 30h8M20 40h8"/></svg><span>Reaming</span></div>
<div class="cap" style="left:203px"><svg width="56" height="60" viewBox="0 0 56 60" fill="none" stroke="#111" stroke-width="2"><path d="M6 4h44v8H6zM22 12h12v12H22zM28 24v10M4 44h48v10H4zM22 38l6-4 6 4"/></svg><span>Parting/Cutting</span></div>
<div class="cap" style="left:407px"><svg width="56" height="60" viewBox="0 0 56 60" fill="none" stroke="#111" stroke-width="2"><circle cx="28" cy="34" r="16"/><circle cx="28" cy="34" r="5"/><path d="M10 10l14 20M4 56h48"/></svg><span>Facing</span></div>
<div class="cap" style="left:610px"><svg width="56" height="60" viewBox="0 0 56 60" fill="none" stroke="#111" stroke-width="2"><path d="M24 4v30M18 34h12v8H18zM4 48h48v8H4zM36 40h12v8"/><circle cx="12" cy="44" r="4"/></svg><span>Turning</span></div>
<div class="cap" style="left:813px"><svg width="56" height="60" viewBox="0 0 56 60" fill="none" stroke="#111" stroke-width="2"><path d="M20 8l12-4 8 12-10 8zM30 24l-8 10M10 34h22v14H10zM6 48h30v8H6zM38 30h12v20H38z"/></svg><span>Boring</span></div>
<div class="cap faded" style="left:1017px"><svg width="56" height="60" viewBox="0 0 56 60" fill="none" stroke="#111" stroke-width="2"><path d="M20 4h16v8H20zM28 12v24M24 20h8M24 28h8M6 36h44v20H6zM6 46h44"/></svg><span>Drilling</span></div>
<div class="slider-arrow" style="left:123px;top:3292px"><svg width="16" height="12" viewBox="0 0 16 12" fill="none" stroke="#fff" stroke-width="1.6"><path d="M15 6H1M6 1L1 6l5 5"/></svg></div>
<div class="slider-arrow" style="left:1037px;top:3292px"><svg width="16" height="12" viewBox="0 0 16 12" fill="none" stroke="#fff" stroke-width="1.6"><path d="M1 6h14M10 1l5 5-5 5"/></svg></div>
<div class="btn-outline" style="left:537px;top:3440px;width:126px;height:38px;font-size:13px">Contact Us</div>

<h2 class="section-title" style="top:3598px">Contact Us</h2>
<div class="field filled" style="left:298px;top:3720px">First Name*</div>
<div class="field" style="left:610px;top:3720px">Last Name*</div>
<div class="field" style="left:298px;top:3796px">Phone Number*</div>
<div class="field" style="left:610px;top:3796px">Postal Code*</div>
<div class="field" style="left:298px;top:3873px;width:604px">Message*</div>
<div class="btn-outline" style="left:550px;top:3980px;width:100px;height:40px">Submit</div>

<footer class="band footer">
  <h4 style="left:163px;top:76px">Quick Links</h4>
  <ul class="quick-links"><li>Home</li><li>About Us</li><li>Services</li><li>Capabilities</li><li>Contact Us</li></ul>
  <div class="foot-brand"><div class="brand-mark"></div><span>NORTHLINE<br>FABRICATION</span></div>
  <h4 style="left:818px;top:76px">Contact Details</h4>
  <div class="contact-row" style="top:118px"><svg width="16" height="18" viewBox="0 0 16 18" fill="#fff"><path d="M8 0a6 6 0 0 0-6 6c0 5 6 12 6 12s6-7 6-12a6 6 0 0 0-6-6zm0 8.5A2.5 2.5 0 1 1 8 3.5a2.5 2.5 0 0 1 0 5z"/></svg><span>123, Building Name, Street<br>City, State XY 123456</span></div>
  <div class="contact-row" style="top:178px"><svg width="16" height="16" viewBox="0 0 16 16" fill="#fff"><path d="M3 1l3 3-2 2c1 2 3 4 6 6l2-2 3 3-2 2C7 15 1 9 1 3z"/></svg><span>(123) 456-7890</span></div>
  <div class="contact-row" style="top:217px"><svg width="16" height="16" viewBox="0 0 16 16" fill="none" stroke="#fff" stroke-width="1.5"><rect x="1" y="3" width="14" height="10"/><path d="M1 3l7 6 7-6"/></svg><span>info@northlinefab.com</span></div>
  <div class="divider"></div>
  <div class="copyright">© 2023 Northline Fabrication. All Rights Reserved.</div>
  <div class="social" style="left:900px"></div>
  <div class="social" style="left:937px"></div>
  <div class="social" style="left:974px"></div>
  <div class="social" style="left:1012px"></div>
</footer>

</body>
</html>
```